Ashmoor DAYS: Final product due on March 4, 2019

We need a newspaper ad for a retirement community called "Tal Roon" located in Manteca, CA. We are estate planning law firm. We would like to include our logo (either blue or white background one) and contents attached (we are flexible to reduce a number of characters), as well as our photo (w/ white background) that will be sent later. We would like to see designs that draw attentions from senior people. You are free to be creative!
Size: 10” wide x 5.5” high
Specs: Artwork must be provided electronically in a pdf format. Color ads must be provided in a color format.

Target Market(s)

Active retirement community in Manteca, CA

Industry/Entity Type

Law Firm

Colors

Designer to choose colors to be used in the design.

Requirements
Must have
• Our logo and contents - see attachments.
• Our photo to be sent tomorrow.
Nice to have
• Use good colors for newspaper ad.
• You are free to be creative.

```html
<!DOCTYPE html>
<html lang="en">
<head>
<meta charset="utf-8">
<title>Harborline Counsel – Newspaper Ad</title>
<link href="https://fonts.googleapis.com/css2?family=Open+Sans:wght@300;400;600;700;800&display=swap" rel="stylesheet">
<style>
  :root {
    --navy: #0f1f5c;
    --gold: #b8862b;
    --white: #ffffff;
    --ink: #1a1a1a;
    --quote: #262626;
    --bubble-light: #f7f7f7;
    --bubble-dark: #dcdcdc;
  }
  * { margin: 0; padding: 0; box-sizing: border-box; }
  html, body { width: 1200px; height: 723px; overflow: hidden; background: var(--white); }
  .ad {
    position: relative;
    width: 1200px;
    height: 723px;
    overflow: hidden;
    font-family: "Open Sans", Arial, sans-serif;
    color: var(--ink);
  }
  .backdrop { position: absolute; inset: 0; }
  .brand {
    position: absolute;
    left: 66px;
    top: 62px;
    font-size: 40px;
    font-weight: 600;
    letter-spacing: 2px;
    color: var(--gold);
    white-space: nowrap;
  }
  .headline {
    position: absolute;
    left: 66px;
    top: 196px;
    font-size: 39px;
    line-height: 53px;
    font-weight: 300;
    color: var(--white);
    white-space: nowrap;
  }
  .headline strong { font-weight: 800; }
  .intro {
    position: absolute;
    left: 66px;
    top: 382px;
    width: 470px;
    font-size: 15px;
    line-height: 22px;
    color: var(--ink);
  }
  .contact {
    position: absolute;
    left: 116px;
    top: 568px;
    color: var(--white);
    font-size: 20px;
    font-weight: 300;
    line-height: 30px;
  }
  .contact-row { display: flex; align-items: flex-start; gap: 10px; }
  .contact-row svg { flex: none; margin-top: 6px; }
  .contact-web { margin-top: 6px; }
  .contact-web strong { font-weight: 700; }
  .testimonial {
    position: absolute;
    left: 520px;
    top: 418px;
    width: 280px;
    text-align: center;
    font-size: 15px;
    line-height: 22px;
    color: var(--ink);
  }
  .quote-mark {
    display: block;
    font-size: 70px;
    font-weight: 800;
    line-height: 40px;
    height: 38px;
    color: var(--quote);
  }
  .quote-mark.open { padding-top: 20px; height: 58px; }
  .quote-mark.close { padding-top: 20px; height: 46px; }
  .testimonial-author { font-weight: 700; margin-top: 8px; }
  .phone {
    position: absolute;
    left: 812px;
    top: 640px;
    display: flex;
    align-items: center;
    gap: 12px;
    color: var(--white);
    font-size: 38px;
    font-weight: 700;
    white-space: nowrap;
  }
</style>
</head>
<body>
<div class="ad">
  <svg class="backdrop" width="1200" height="723" viewBox="0 0 1200 723">
    <defs>
      <linearGradient id="photoTone" x1="0" y1="0" x2="1" y2="1">
        <stop offset="0" stop-color="#c9b79a"/>
        <stop offset="0.45" stop-color="#6f6455"/>
        <stop offset="1" stop-color="#2e2a26"/>
      </linearGradient>
      <radialGradient id="bubbleTone" cx="0.45" cy="0.4" r="0.65">
        <stop offset="0" stop-color="var(--bubble-light)"/>
        <stop offset="1" stop-color="var(--bubble-dark)"/>
      </radialGradient>
    </defs>
    <rect width="1200" height="723" fill="var(--white)"/>
    <rect class="headline-band" x="0" y="161" width="650" height="197" fill="var(--navy)"/>
    <path class="gold-wave" d="M0,600 C140,535 330,500 470,528 C560,548 640,610 700,690 C860,660 1040,560 1200,455 L1200,723 L0,723 Z" fill="var(--gold)"/>
    <path class="contact-wave" d="M0,705 C70,600 200,522 320,522 C430,522 510,600 548,723 L0,723 Z" fill="var(--navy)"/>
    <ellipse cx="891" cy="251" rx="310" ry="323" fill="var(--white)"/>
    <ellipse class="photo" cx="891" cy="251" rx="297" ry="310" fill="url(#photoTone)" role="img" aria-label="Photo of an attorney and client reviewing documents at a desk with scales of justice and a gavel"/>
    <path d="M540,440 A160,168 0 0 0 665,713" fill="none" stroke="var(--navy)" stroke-width="1.2"/>
    <path d="M800,430 A160,168 0 0 1 810,505" fill="none" stroke="var(--navy)" stroke-width="1.2"/>
    <ellipse class="bubble" cx="660" cy="556" rx="150" ry="157" fill="var(--white)"/>
    <ellipse cx="660" cy="556" rx="143" ry="150" fill="url(#bubbleTone)"/>
  </svg>

  <div class="brand">HARBORLINE COUNSEL</div>

  <h1 class="headline">
    Taking care of <strong>your family,</strong><br>
    <strong>finances,</strong> and <strong>healthcare</strong><br>
    is so vitally <strong>important.</strong>
  </h1>

  <p class="intro">ATTORNEY OWEN CASTELL has helped hundreds of Sacramento and Manteca area residents protect themselves and their families. We are located in a convenient location in Manteca—just on the corner of Orchard and Maple, ONLY A SEVEN MINUTE DRIVE FROM TAL ROON! We also do house calls!</p>

  <div class="contact">
    <div class="contact-row">
      <svg width="14" height="20" viewBox="0 0 14 20" aria-hidden="true">
        <circle cx="7" cy="6" r="4.5" fill="none" stroke="var(--white)" stroke-width="1.6"/>
        <path d="M7,10.5 L7,16" stroke="var(--white)" stroke-width="1.6"/>
        <path d="M2,17.5 L12,17.5" stroke="var(--white)" stroke-width="1.6"/>
      </svg>
      <div>Estate Planning Law Firm<br>2480 East Orchard Lane,<br>Suite #210, Manteca CA 95337</div>
    </div>
    <div class="contact-row contact-web">
      <svg width="18" height="18" viewBox="0 0 18 18" aria-hidden="true">
        <circle cx="9" cy="9" r="7.5" fill="none" stroke="var(--white)" stroke-width="1.4"/>
        <ellipse cx="9" cy="9" rx="3.2" ry="7.5" fill="none" stroke="var(--white)" stroke-width="1.2"/>
        <path d="M1.5,9 H16.5 M3,5 H15 M3,13 H15" stroke="var(--white)" stroke-width="1.1"/>
      </svg>
      <div>www.<strong>HarborlineLaw</strong>.com</div>
    </div>
  </div>

  <blockquote class="testimonial">
    <span class="quote-mark open">“</span>
    <p>What we like the best is there is never a cost to speak with Owen about our estate plan. We got all our questions answered and had great peace of mind after working with him!</p>
    <p class="testimonial-author">Dale &amp; Nora</p>
    <span class="quote-mark close">”</span>
  </blockquote>

  <div class="phone">
    <svg width="40" height="40" viewBox="0 0 40 40" aria-hidden="true">
      <circle cx="20" cy="20" r="18" fill="none" stroke="var(--white)" stroke-width="2.5"/>
      <path d="M14,11 L17.5,11 L19,16 L16.8,17.6 C17.8,20.2 19.8,22.2 22.4,23.2 L24,21 L29,22.5 L29,26 C29,27.5 27.5,29 26,29 C18.5,28.5 11.5,21.5 11,14 C11,12.5 12.5,11 14,11 Z" fill="var(--white)"/>
    </svg>
    <span>(209) 555-0148</span>
  </div>
</div>
</body>
</html>
```